Create a memorable Stationary for Security Software Company

Velbrantix is the worldwide leader in securing the Internet. Making Internet communications and critical data secure, reliable and available everywhere has been and continues to be our ongoing vision. We are committed to staying focused on real customer needs and to developing new and innovative security solutions that redefine the security landscape.

Industry/Entity Type

Internet

Font styles to use
Serif
Sans Serif
Script

Colors
0792cd
33a6d7
85cae6

```html
<!DOCTYPE html>
<html lang="en">
<head>
<meta charset="utf-8">
<title>Velbrantix Business Card</title>
<link rel="stylesheet" href="https://fonts.googleapis.com/css2?family=Source+Sans+3:wght@400;600;700&display=swap">
<style>
  :root {
    --blue-deep: #0792cd;
    --blue-mid: #33a6d7;
    --blue-light: #85cae6;
    --ink: #4a4a4a;
    --rule: #9a9a9a;
    --paper: #ffffff;
    --night: #000000;
    --backdrop: #e9e4dc;
  }
  * { margin: 0; padding: 0; box-sizing: border-box; }
  html, body {
    width: 1200px; height: 1118px; overflow: hidden;
    background: var(--backdrop);
    font-family: "Source Sans 3", sans-serif;
  }
  .canvas { position: relative; width: 1200px; height: 1118px; }

  .card {
    position: absolute;
    width: 820px; height: 468px;
    border-radius: 36px;
    overflow: hidden;
  }
  .card-front { left: 40px; top: 54px; background: var(--paper); border: 1px solid #555; }
  .card-back { left: 332px; top: 591px; background: var(--night); }

  .brand {
    position: absolute;
    display: flex; align-items: center; gap: 12px;
    color: var(--blue-mid);
    font-weight: 700; font-size: 46px; letter-spacing: 0.5px;
    transform: translate(-50%, -50%);
    white-space: nowrap;
  }
  .brand-dot {
    width: 30px; height: 30px; border-radius: 50%;
    background: var(--blue-mid);
  }
  .card-front .brand { left: 239px; top: 233px; }
  .card-back .brand { left: 410px; top: 191px; }

  .divider {
    position: absolute; left: 445px; top: 72px;
    width: 1px; height: 271px; background: var(--rule);
  }
  .details { position: absolute; left: 479px; top: 74px; color: var(--ink); }
  .person-name { color: var(--blue-deep); font-weight: 700; font-size: 27px; line-height: 34px; }
  .person-title { font-size: 23px; line-height: 30px; letter-spacing: 0.5px; margin-bottom: 12px; }
  .contact-list { list-style: none; }
  .contact-list li {
    display: flex; align-items: center; gap: 8px;
    font-size: 20px; line-height: 33.5px;
  }
  .contact-list svg { width: 17px; height: 17px; flex: none; }
  .address { font-size: 20px; line-height: 28px; margin-top: 12px; }

  .footer-band {
    position: absolute; left: 0; bottom: 0;
    width: 100%; height: 84px;
    background: linear-gradient(180deg, var(--blue-light) 0%, var(--blue-mid) 45%, var(--blue-deep) 100%);
  }

  .web-address {
    position: absolute; left: 0; right: 0; top: 355px;
    text-align: center; color: var(--paper);
    font-size: 26px; letter-spacing: 5px;
  }
</style>
</head>
<body>
<div class="canvas">

  <section class="card card-front">
    <div class="brand"><span class="brand-dot"></span>Velbrantix</div>
    <div class="divider"></div>
    <div class="details">
      <p class="person-name">Your Name</p>
      <p class="person-title">Title</p>
      <ul class="contact-list">
        <li>
          <svg viewBox="0 0 16 16" aria-hidden="true"><circle cx="8" cy="8" r="7" fill="none" stroke="#0792cd" stroke-width="1.5"/><path d="M5 4.5c0 4 2.5 7 6.5 7l.5-1.8-2-1-1 1c-1.3-.7-2.2-1.6-2.8-2.8l1-1-1-2z" fill="#0792cd"/></svg>
          012-345-6789
        </li>
        <li>
          <svg viewBox="0 0 16 16" aria-hidden="true"><rect x="4" y="1" width="8" height="14" rx="1.5" fill="#0792cd"/><rect x="5.5" y="3" width="5" height="4" fill="#fff"/><circle cx="8" cy="11.5" r="1.2" fill="#fff"/></svg>
          012-345-6789
        </li>
        <li>
          <svg viewBox="0 0 16 16" aria-hidden="true"><path d="M1 6 8 2l7 4v8H1z" fill="#0792cd"/><path d="M1 6l7 4.5L15 6" fill="none" stroke="#fff" stroke-width="1.3"/></svg>
          info@velbrantix.com
        </li>
        <li>
          <svg viewBox="0 0 16 16" aria-hidden="true"><g fill="none" stroke="#0792cd" stroke-width="1.3"><circle cx="8" cy="8" r="6.5"/><ellipse cx="8" cy="8" rx="3" ry="6.5"/><path d="M1.5 8h13M2.8 4.5h10.4M2.8 11.5h10.4"/></g></svg>
          www.velbrantix.com
        </li>
      </ul>
      <p class="address">Street Name, City Name<br>Zipcode-012345</p>
    </div>
    <div class="footer-band" role="img" aria-label="Decorative blue wave band along the bottom edge"></div>
  </section>

  <section class="card card-back">
    <div class="brand"><span class="brand-dot"></span>Velbrantix</div>
    <p class="web-address">www.velbrantix.com</p>
  </section>

</div>
</body>
</html>
```